Updated website design needed for Radiology Group, Pine Hollow Imaging Partners

Clean, uncluttered, updated design needed for top regional Radiology Center. Focus on personal, patient oriented design, (not clinical). Should be simple and easy to navigate, with clear CTAs. Use blues, greens and photos of people in the Central Oregon outdoors.
Uncoded, PSD design only. 2 pages: Home page and one example interior page.
reference current site: http://www.phipclinic-example.com/
Sites they like:
http://www.valescanlabs-example.com/
http://www.tbmx-example.net/handler.cfm?event=practice,main
http://www.kestrelbonecare-example.com/

Medical Imaging

2 page

Sans Serif

• Personal and patient friendly.
• Lots of white space, clean and uncluttered. Clear CTAs, such as: Patient Bill Pay, Make an Appointment, Meet Our Doctors
• Use copy and contact information from the current site.
• Use outdoor images from Central Oregon, late Winter/ Spring (snow, light colors, spring green, for example)
• Include one example interior page, either Your Exam or Meet Our Doctors
• The client likes:
• Meet Our Doctors slider section, and big, easy to navigate Information Center on www.kestrelbonecare-example.com
• The personal feel of the Your Exam section on www.valescanlabs-example.com
• Blues and Greens, outdoorsy imagery
• The client does not like:
• complex drop down menus
• clinical feel
• Do not use lorum ipsum or dummy text.
• Do not use outdoor images from other regions. Do not use Summer (hot, poolside) or Fall (red/orange leaves) images.

```html
<!DOCTYPE html>
<html lang="en">
<head>
<meta charset="utf-8">
<title>Pine Hollow Imaging Partners</title>
<link rel="stylesheet" href="https://fonts.googleapis.com/css2?family=Lato:wght@400;700;900&family=Montserrat:wght@400;500;600;700&display=swap">
<style>
:root{
  --brand:#2f7ea6;
  --brand-dark:#22607f;
  --accent:#3f8f78;
  --ink:#1b1b1b;
  --text:#6d6d6d;
  --muted:#8a8a8a;
  --nav:#050505;
  --footer:#e3e3e3;
  --line:#c9c9c9;
  --white:#ffffff;
  --btn-grey:#6e6e6e;
}
*{box-sizing:border-box;margin:0;padding:0}
html,body{width:1200px;height:2568px;overflow:hidden;background:#fff}
body{position:relative;font-family:"Lato",sans-serif;color:var(--text)}
.abs{position:absolute}
a{color:inherit;text-decoration:none}

/* header */
.site-header{left:0;top:0;width:1200px;height:99px;background:#fff}
.brand{left:46px;top:12px;display:flex;align-items:center;gap:12px}
.brand-mark{width:76px;height:76px;background:var(--brand)}
.brand-name{font-family:"Lato",sans-serif;font-size:25px;line-height:28px;color:var(--ink);width:190px}
.contact-box{top:20px;width:157px;height:57px;background:var(--brand);color:#fff;text-align:center;padding-top:8px}
.contact-box .label{font-family:"Montserrat",sans-serif;font-size:16px;font-weight:500}
.contact-box .num{font-size:13px;margin-top:2px;display:flex;justify-content:center;align-items:center;gap:4px}

/* nav */
.main-nav{left:0;top:99px;width:1200px;height:64px;background:var(--nav);display:flex;align-items:center;padding-left:48px}
.main-nav a{font-size:14px;color:#fff;padding:0 20px;position:relative;height:64px;line-height:64px}
.main-nav a+a::before{content:"";position:absolute;left:0;top:26px;height:13px;width:1px;background:#fff}
.main-nav a.active{background:var(--brand);padding:0 21px}

/* hero */
.hero{left:0;top:163px;width:1200px;height:467px;background:linear-gradient(90deg,#dfe6e2 0%,#c4d2cc 30%,#a9bcc2 55%,#c9d5d8 80%,#9fb2b8 100%)}
.hero-photo{left:0;top:0;width:1200px;height:467px}
.hero-copy{left:400px;top:134px;color:#fff}
.hero-copy .kicker{font-size:28px;font-weight:700;white-space:nowrap}
.hero-copy h1{font-size:72px;font-weight:700;line-height:80px;margin-top:2px;white-space:nowrap}
.hero-copy .sub{font-size:17px;font-weight:700;margin-top:6px;white-space:nowrap}
.btn{display:inline-block;font-size:13px;text-align:center;text-transform:uppercase}
.btn-brand{background:var(--brand);color:#fff}
.hero-copy .btn{margin-top:14px;width:120px;height:44px;line-height:44px}
.slide-arrow{top:229px;width:36px;height:36px;border-radius:50%;background:#fff;display:flex;align-items:center;justify-content:center}
.dots{left:467px;top:413px;display:flex;gap:6px}
.dots span{width:13px;height:13px;border-radius:50%;border:1.5px solid #fff}
.dots span.on{background:#fff}

/* cta band */
.cta-band{left:0;top:630px;width:1200px;height:173px;background:var(--accent)}
.cta{top:45px;display:flex;gap:24px}
.cta-icon{width:74px;height:74px;border-radius:50%;background:#fff;display:flex;align-items:center;justify-content:center;flex:none}
.cta h3{font-family:"Montserrat",sans-serif;font-weight:400;font-size:21px;color:#fff;border-bottom:1px solid #fff;padding-bottom:6px;width:236px;white-space:nowrap}
.cta p{font-size:12.5px;color:#fff;line-height:20px;margin-top:6px;width:236px}

/* welcome */
.welcome{left:0;top:803px;width:1200px;height:275px;text-align:center}
.welcome h2{font-family:"Montserrat",sans-serif;font-size:31px;font-weight:700;color:var(--ink);margin-top:38px}
.welcome h2 span{color:var(--brand)}
.welcome p{width:1000px;margin:22px auto 0;font-size:12px;line-height:21px;color:var(--text)}
.welcome .btn{margin-top:30px;width:125px;height:38px;line-height:38px;font-size:12px}

/* mri band */
.mri-band{left:0;top:1078px;width:1200px;height:288px;background:radial-gradient(ellipse at 55% 30%,#25424e 0%,#122a33 55%,#0a1519 100%);text-align:center;color:#fff}
.notch{left:588px;top:0;width:0;height:0;border-left:12px solid transparent;border-right:12px solid transparent;border-top:14px solid #fff}
.mri-band h2{font-family:"Lato",sans-serif;font-weight:700;font-size:33px;padding-top:66px}
.mri-band p{width:800px;margin:12px auto 0;font-size:16px;line-height:26px}
.mri-band .btn{margin-top:26px;width:149px;height:38px;line-height:38px;background:#fff;color:#222;font-size:13px}

/* vc */
.vc-image{left:51px;top:1443px;width:271px;height:221px;background:linear-gradient(135deg,#c8dcec 0%,#7aa3c6 45%,#3b6d9a 100%)}
.vc-copy{left:366px;top:1440px;width:775px}
.vc-copy h2{font-family:"Montserrat",sans-serif;font-size:21px;font-weight:600;color:var(--brand)}
.vc-copy p{font-size:11.5px;line-height:23px;color:var(--muted);margin-top:14px}
.vc-copy .btn{margin-top:22px;width:122px;height:36px;line-height:36px;font-size:12px}

/* features */
.features{left:0;top:1760px;width:1200px;height:448px;background:radial-gradient(ellipse at 70% 50%,#2f3337 0%,#1a1c1f 60%,#0e0f11 100%)}
.features h2{position:absolute;left:0;top:45px;width:1200px;text-align:center;font-family:"Montserrat",sans-serif;font-size:31px;font-weight:500;color:#fff}
.view-all{left:1027px;top:84px;font-size:11px;color:#fff;font-weight:700}
.feature-row{left:77px;width:1044px;height:77px;background:rgba(80,82,88,.75)}
.feature-icon{position:absolute;left:47px;top:11px;width:55px;height:55px;border-radius:50%;background:#fff;display:flex;align-items:center;justify-content:center}
.feature-row .div1,.feature-row .div2{position:absolute;top:16px;width:1px;height:45px;background:#9a9a9a}
.feature-row .div1{left:132px}
.feature-row .div2{left:428px}
.feature-name{position:absolute;left:150px;top:0;height:77px;width:260px;display:flex;align-items:center;justify-content:center;text-align:center;font-family:"Montserrat",sans-serif;font-size:16px;font-weight:600;color:#fff;line-height:20px}
.feature-text{position:absolute;left:462px;top:0;height:77px;width:430px;display:flex;align-items:center;font-size:11.5px;line-height:18px;color:#fff}
.feature-btn{position:absolute;left:902px;top:21px;width:112px;height:35px;line-height:35px;background:var(--btn-grey);color:#fff;font-size:12.5px;text-align:center}

/* footer */
.site-footer{left:0;top:2208px;width:1200px;height:266px;background:var(--footer)}
.col-divider{top:26px;width:1px;height:214px;background:var(--line)}
.footer-col h4{font-family:"Montserrat",sans-serif;font-size:16px;font-weight:500;color:var(--brand);letter-spacing:.5px}
.careers-image{left:51px;top:83px;width:370px;height:89px;background:linear-gradient(90deg,#b9c0c9 0%,#7b8594 40%,#2d3a52 75%,#c3c7cf 100%)}
.careers-text{left:51px;top:182px;width:375px;font-size:12px;line-height:17px;color:#333}
.newsletter p{font-size:12px;line-height:17px;color:#333;margin-top:20px;width:320px}
.email-input{width:318px;height:36px;background:#fff;border:1px solid #ddd;margin-top:12px;font-size:10px;color:#aaa;padding:12px 12px}
.subscribe{width:318px;height:38px;background:#4a4a4a;color:#fff;font-size:14px;text-align:center;line-height:38px;margin-top:7px;font-family:"Montserrat",sans-serif}
.location ul{list-style:none;margin-top:18px}
.location li{display:flex;gap:18px;font-size:12.5px;color:#333;line-height:19px;margin-bottom:3px}
.location li svg{flex:none;margin-top:3px}

/* bottom bar */
.copyright-bar{left:0;top:2474px;width:1200px;height:94px;background:var(--brand)}
.copyright-bar p{position:absolute;left:0;top:40px;width:1200px;text-align:center;font-size:12.5px;color:#fff}
.social{top:32px;width:29px;height:29px;border:1.5px solid #fff;display:flex;align-items:center;justify-content:center}
.social span{width:10px;height:10px;background:#fff}
</style>
</head>
<body>

<header class="site-header abs">
  <div class="brand abs">
    <div class="brand-mark"></div>
    <div class="brand-name">Pine Hollow Imaging Partners</div>
  </div>
  <div class="contact-box abs" style="left:479px">
    <div class="label">Medical Records:</div>
    <div class="num"><svg width="10" height="10" viewBox="0 0 10 10"><path d="M2 1l2 2-1 1.2a6 6 0 0 0 2.8 2.8L7 6l2 2-1.3 1.3C4.5 9 1 5.5.7 2.3z" fill="#fff"/></svg>+ (555) 214-7730</div>
  </div>
  <div class="contact-box abs" style="left:661px">
    <div class="label">Billing:</div>
    <div class="num"><svg width="10" height="10" viewBox="0 0 10 10"><path d="M2 1l2 2-1 1.2a6 6 0 0 0 2.8 2.8L7 6l2 2-1.3 1.3C4.5 9 1 5.5.7 2.3z" fill="#fff"/></svg>+ (555) 214-7742</div>
  </div>
  <div class="contact-box abs" style="left:830px">
    <div class="label">Scheduling:</div>
    <div class="num"><svg width="10" height="10" viewBox="0 0 10 10"><path d="M2 1l2 2-1 1.2a6 6 0 0 0 2.8 2.8L7 6l2 2-1.3 1.3C4.5 9 1 5.5.7 2.3z" fill="#fff"/></svg>+ (555) 214-7768</div>
  </div>
  <div class="contact-box abs" style="left:1000px">
    <div class="label">Main Line:</div>
    <div class="num"><svg width="10" height="10" viewBox="0 0 10 10"><path d="M2 1l2 2-1 1.2a6 6 0 0 0 2.8 2.8L7 6l2 2-1.3 1.3C4.5 9 1 5.5.7 2.3z" fill="#fff"/></svg>+ (555) 214-7700</div>
  </div>
</header>

<nav class="main-nav abs">
  <a class="active">Home</a>
  <a>About Us</a>
  <a>Our Service</a>
  <a>For Patients</a>
  <a>Our Physicians</a>
  <a>For Physicians</a>
  <a>PACS &amp; Document</a>
  <a>Appointment</a>
  <a>Our Location</a>
</nav>

<section class="hero abs">
  <div class="hero-photo abs" role="img" aria-label="Smiling physician in a white coat holding a folder, with a bright imaging room softly blurred behind her"></div>
  <div class="hero-copy abs">
    <div class="kicker">Welcome to Pine Hollow Imaging Partners</div>
    <h1>Diagnostic Imaging</h1>
    <div class="sub">Corporation Providing Professional services to Centraand Eastern Oregon hospital</div>
    <a class="btn btn-brand">Read More</a>
  </div>
  <div class="slide-arrow abs" style="left:30px"><svg width="12" height="12" viewBox="0 0 12 12"><path d="M8 1L3 6l5 5" fill="none" stroke="#222" stroke-width="2"/></svg></div>
  <div class="slide-arrow abs" style="left:1134px"><svg width="12" height="12" viewBox="0 0 12 12"><path d="M4 1l5 5-5 5" fill="none" stroke="#222" stroke-width="2"/></svg></div>
  <div class="dots abs"><span></span><span></span><span class="on"></span><span></span><span></span></div>
</section>

<section class="cta-band abs">
  <div class="cta abs" style="left:61px">
    <div class="cta-icon"><svg width="30" height="36" viewBox="0 0 30 36"><path d="M5 4h20M5 12h20M5 4h6a8 8 0 0 1 0 16H5l14 14" fill="none" stroke="var(--accent)" stroke-width="3.5" stroke-linejoin="round"/></svg></div>
    <div><h3>Patient Bill Pay</h3><p>Pay your statement online in a few easy and secure steps &#9656;</p></div>
  </div>
  <div class="cta abs" style="left:432px">
    <div class="cta-icon"><svg width="34" height="38" viewBox="0 0 34 38"><rect x="5" y="6" width="24" height="30" fill="none" stroke="var(--accent)" stroke-width="3"/><path d="M13 12h8M17 8v8M11 22h4M19 22h4M11 28h4M19 28h4" stroke="var(--accent)" stroke-width="2.5"/></svg></div>
    <div><h3>Make an Appointment</h3><p>Choose a time that suits you and our team will confirm it &#9656;</p></div>
  </div>
  <div class="cta abs" style="left:810px">
    <div class="cta-icon"><svg width="36" height="36" viewBox="0 0 36 36"><circle cx="18" cy="11" r="7" fill="none" stroke="var(--accent)" stroke-width="3"/><path d="M5 34c0-8 6-13 13-13s13 5 13 13z" fill="none" stroke="var(--accent)" stroke-width="3"/><circle cx="18" cy="28" r="2.5" fill="var(--accent)"/></svg></div>
    <div><h3>Meet Our Doctors</h3><p>Get to know the radiologists who read and explain your exam &#9656;</p></div>
  </div>
</section>

<section class="welcome abs">
  <h2>Welcome to <span>Pine Hollow Imaging Partners</span></h2>
  <p>For more than three decades our radiologists have cared for families across Central and Eastern Oregon. We believe an imaging visit should feel calm and personal, so our technologists take time to explain each step, answer your questions and keep you comfortable. Your doctor receives clear, timely results, and you receive the respect and attention you deserve. From routine X-rays to advanced MRI, we are proud to be your neighbors in care.</p>
  <a class="btn btn-brand">Read More</a>
</section>

<section class="mri-band abs">
  <div class="notch abs"></div>
  <h2>NEW Norvale 3T MRI VANTIS Prime</h2>
  <p>Pine Hollow MRI has acquired the most exciting innovation in MRI. Norvale brings together the strongest magnet in Central Oregon with the 70 cm Open Bore for one powerful system.</p>
  <a class="btn">Read More</a>
</section>

<div class="vc-image abs" role="img" aria-label="Close-up of a pen resting on a printed medical chart in blue tones"></div>
<section class="vc-copy abs">
  <h2>Virtual Colonoscopy (VC),</h2>
  <p>Virtual colonoscopy uses a low-dose CT scan to create detailed three-dimensional views of the colon and rectum. It is a gentle screening option for many adults, with no sedation and no scope, and most patients return to normal activities the same day. Before your exam our staff will walk you through the simple preparation and answer any questions. During the scan you lie comfortably on the table for about fifteen minutes while images are taken. A radiologist reviews every image carefully and sends a clear report to your doctor, who will talk with you about the results and next steps.</p>
  <a class="btn btn-brand">Read More</a>
</section>

<section class="features abs">
  <div class="notch abs"></div>
  <h2>Our Feature</h2>
  <div class="view-all abs">View All</div>

  <div class="feature-row abs" style="top:115px">
    <div class="feature-icon"><svg width="24" height="20" viewBox="0 0 24 20"><circle cx="12" cy="6" r="4" fill="var(--brand)"/><circle cx="5" cy="8" r="3" fill="var(--brand)"/><circle cx="19" cy="8" r="3" fill="var(--brand)"/><path d="M5 19c0-5 3-8 7-8s7 3 7 8zM0 18c0-4 2-6 5-6l1 .2C4.5 14 4 16 4 18zM24 18c0-4-2-6-5-6l-1 .2c1.5 1.8 2 3.8 2 5.8z" fill="var(--brand)"/></svg></div>
    <span class="div1"></span><span class="div2"></span>
    <div class="feature-name">Magnetic Resonance<br>Imaging (MRI)</div>
    <div class="feature-text">Detailed images of joints, brain and soft tissue on our wide, open bore scanner, with music to help you relax.</div>
    <a class="feature-btn">Read More</a>
  </div>

  <div class="feature-row abs" style="top:212px">
    <div class="feature-icon"><svg width="22" height="22" viewBox="0 0 22 22"><circle cx="11" cy="11" r="10" fill="var(--brand)"/><circle cx="11" cy="11" r="3.5" fill="#fff"/><circle cx="11" cy="4" r="1.6" fill="#fff"/><circle cx="11" cy="18" r="1.6" fill="#fff"/><circle cx="4" cy="11" r="1.6" fill="#fff"/><circle cx="18" cy="11" r="1.6" fill="#fff"/></svg></div>
    <span class="div1"></span><span class="div2"></span>
    <div class="feature-name">Digital Mammography</div>
    <div class="feature-text">Gentle, low-dose 3D breast screening with caring female technologists and fast results sent to your doctor.</div>
    <a class="feature-btn">Read More</a>
  </div>

  <div class="feature-row abs" style="top:308px">
    <div class="feature-icon"><svg width="24" height="22" viewBox="0 0 24 22"><path d="M6 2l6 4-6 4-6-4zM18 2l6 4-6 4-6-4zM6 10l6 4-6 4-6-4zM18 10l6 4-6 4-6-4z" fill="var(--brand)"/></svg></div>
    <span class="div1"></span><span class="div2"></span>
    <div class="feature-name">Computed Tomography<br>(CT)</div>
    <div class="feature-text">Quick, precise scans of the chest, abdomen and head using the lowest dose needed for a clear answer.</div>
    <a class="feature-btn">Read More</a>
  </div>
</section>

<footer class="site-footer abs">
  <div class="footer-col abs" style="left:56px;top:40px"><h4>CAREES</h4></div>
  <div class="careers-image abs" role="img" aria-label="Two business people in suits shaking hands"></div>
  <p class="careers-text abs">Join a friendly team of technologists, nurses and radiologists who care about patients and each other. See our open positions today &#9656;</p>

  <span class="col-divider abs" style="left:469px"></span>

  <div class="footer-col newsletter abs" style="left:526px;top:40px">
    <h4>NEWSLETTER SIGNUP</h4>
    <p>Subscribe our newsletter to know our daily updates and offer daily updates and offerpsun dolor sit amet elit, sed aliqua.</p>
    <div class="email-input">Enter your Email Id</div>
    <div class="subscribe">SUBSCRIBE</div>
  </div>

  <span class="col-divider abs" style="left:889px"></span>

  <div class="footer-col location abs" style="left:947px;top:40px">
    <h4>LOCATION</h4>
    <ul>
      <li><svg width="9" height="12" viewBox="0 0 9 12"><path d="M4.5 0A4.5 4.5 0 0 0 0 4.5C0 8 4.5 12 4.5 12S9 8 9 4.5A4.5 4.5 0 0 0 4.5 0z" fill="var(--brand)"/><circle cx="4.5" cy="4.5" r="1.6" fill="#fff"/></svg><span>Address Line1,<br>Address Line-2<br>Country - 123456</span></li>
      <li><svg width="11" height="11" viewBox="0 0 10 10"><path d="M2 1l2 2-1 1.2a6 6 0 0 0 2.8 2.8L7 6l2 2-1.3 1.3C4.5 9 1 5.5.7 2.3z" fill="var(--brand)"/></svg><span>Office:&nbsp; 123.456.789</span></li>
      <li><svg width="11" height="11" viewBox="0 0 11 11"><rect x="1" y="3" width="9" height="7" fill="var(--brand)"/><rect x="3" y="0" width="5" height="3" fill="var(--brand)"/></svg><span>Fax:&nbsp; 123.456.789</span></li>
      <li><svg width="11" height="11" viewBox="0 0 11 11"><rect x="0" y="1" width="11" height="9" fill="var(--brand)"/><path d="M0 2l5.5 4L11 2" fill="none" stroke="#fff" stroke-width="1"/></svg><span>info@companyname.com</span></li>
    </ul>
  </div>
</footer>

<div class="copyright-bar abs">
  <p>Copyright 2016 Company Name.&nbsp; All Rights Reserved.</p>
  <div class="social abs" style="left:1039px"><span></span></div>
  <div class="social abs" style="left:1080px"><span></span></div>
  <div class="social abs" style="left:1123px"><span></span></div>
</div>

</body>
</html>
```